Brightfen Business Card Redesign & Logo Update

We need to update our business cards to something more modern and fresh. Brightfen can provide the current color schemes and old design examples, but welcome creativity in helping us with this redesign. PLEASE NOTE that we no longer utilize the "tree" and/or "leaf" imagery in our branding. If able would apprecaite an update on the quality of our "words only" logo in Ai. / PNG formats too.

Target Market(s)

Investors, landowners, corporate partners, contractors

Industry/Entity Type

Environmental Restoration & Conservation

Contact Information for Business Card

Logo, persons name, title, mailing address, phone and email, website url

Font styles to use
Other font styles liked:
• Merriweather

Requirements
Nice to have
• Logo, persons name, title, mailing address, phone and email, website url, but open to ideams
Should not have
• No all back backgrounds

```html
<!DOCTYPE html>
<html lang="en">
<head>
<meta charset="utf-8">
<title>Brightfen Business Card</title>
<link href="https://fonts.googleapis.com/css2?family=Open+Sans:wght@400;800&display=swap" rel="stylesheet">
<style>
  :root {
    --stage: #dcdcda;
    --paper: #ffffff;
    --brand-green: #137a3c;
    --brand-orange: #ee7b22;
    --muted: #444444;
  }
  * { margin: 0; padding: 0; box-sizing: border-box; }
  html, body { width: 1200px; height: 801px; overflow: hidden; }
  body {
    background: var(--stage);
    font-family: "Open Sans", sans-serif;
    display: flex;
    align-items: center;
    justify-content: center;
    gap: 60px;
  }
  .card {
    position: relative;
    width: 520px;
    height: 297px;
    background: var(--paper);
    border-bottom: 3px solid var(--brand-green);
    box-shadow: 0 10px 26px rgba(0,0,0,0.18);
  }
  .brand-name {
    display: flex;
    align-items: center;
    gap: 10px;
    font-weight: 800;
    color: var(--brand-green);
    line-height: 1;
  }
  .brand-name .dot {
    width: 14px; height: 14px; border-radius: 50%;
    background: var(--brand-orange); flex: none;
  }
  /* Front: contact side */
  .card--front .brand-name {
    position: absolute; left: 38px; top: 96px; font-size: 30px;
  }
  .person { position: absolute; right: 38px; top: 40px; text-align: right; }
  .person .full-name {
    font-weight: 800; font-size: 17px; color: var(--brand-green); letter-spacing: 0.5px;
  }
  .person .title { font-size: 12px; color: var(--muted); margin-top: 2px; }
  .divider {
    position: absolute; left: 38px; right: 38px; top: 172px;
    height: 1px; background: var(--brand-green);
  }
  .address {
    position: absolute; right: 38px; top: 186px; text-align: right;
    font-size: 12px; line-height: 1.6; color: var(--muted);
  }
  .contacts {
    position: absolute; left: 38px; top: 190px; list-style: none;
    font-size: 12px; line-height: 1.75; color: var(--muted);
  }
  .contacts li { display: flex; align-items: center; gap: 8px; }
  .contacts svg { width: 11px; height: 11px; flex: none; }
  /* Back: name side */
  .card--back { display: flex; align-items: center; justify-content: center; }
  .card--back .brand-name { font-size: 54px; gap: 16px; }
  .card--back .brand-name .dot { width: 24px; height: 24px; }
</style>
</head>
<body>
  <section class="card card--front">
    <div class="brand-name"><span class="dot"></span>Brightfen</div>
    <div class="person">
      <div class="full-name">DARA VELLING</div>
      <div class="title">President</div>
    </div>
    <div class="divider"></div>
    <div class="address">
      1180 Harbor Crest Dr<br>
      Bayview CA 90000
    </div>
    <ul class="contacts">
      <li>
        <svg viewBox="0 0 12 12" aria-hidden="true"><path d="M2.5 1h2l1 3-1.5 1a6 6 0 0 0 3 3l1-1.5 3 1v2c0 .8-.7 1.5-1.5 1.5A10 10 0 0 1 1 2.5C1 1.7 1.7 1 2.5 1z" fill="var(--brand-orange)"/></svg>
        555-014-2290
      </li>
      <li>
        <svg viewBox="0 0 12 12" aria-hidden="true"><rect x="1" y="2.5" width="10" height="7" rx="1" fill="var(--brand-orange)"/><path d="M1.5 3l4.5 3.5L10.5 3" stroke="#fff" stroke-width="1" fill="none"/></svg>
        dvelling@brightfen.com
      </li>
      <li>
        <svg viewBox="0 0 12 12" aria-hidden="true"><circle cx="6" cy="6" r="5" fill="var(--brand-orange)"/><path d="M1 6h10M6 1c-2 2.5-2 7.5 0 10M6 1c2 2.5 2 7.5 0 10" stroke="#fff" stroke-width="0.8" fill="none"/></svg>
        www.brightfen.com
      </li>
    </ul>
  </section>

  <section class="card card--back">
    <div class="brand-name"><span class="dot"></span>Brightfen</div>
  </section>
</body>
</html>
```